Brimlow OrthoLink IT Inc. new website

i need a website for my company which is dedicated to installation and service of computer systems in Dental Offices. I would like for it to encompass a technology feel and professional look. The company deals with all aspects of technology like, Audio Visual, computer systems and networks, Cloud services like data backup, data center. We provide manage services, support and services to Dental Professionals.
Updates

Looking for a Technology font but professional look Added Wednesday, April 20, 2016

Target Market(s)

Dental, Dentist

Industry/Entity Type

Dental

Number of Pages Required

5+ page

Font styles to use
Other font styles liked:
• Futuristic or Techy

Colors
0255a3
ec1f27

Requirements
Must have
• Tabs
Nice to have
• Have no idea maybe some suggestion on your part may help
Should not have
• A professional feel but have a techy look

```html
<!DOCTYPE html>
<html lang="en">
<head>
<meta charset="utf-8">
<title>Brimlow OrthoLink IT Inc.</title>
<link rel="stylesheet" href="https://fonts.googleapis.com/css2?family=Raleway:ital,wght@0,400;0,500;0,600;0,700;1,400&display=swap">
<style>
:root{
  --blue:#0255a3;
  --blue-dark:#014a8f;
  --red:#ec1f27;
  --text:#555;
  --dark:#222;
  --light:#f5f5f5;
  --gray-band:#efefef;
  --footer:#3b3b3b;
  --white:#fff;
}
*{box-sizing:border-box;margin:0;padding:0}
html,body{width:1200px;height:2903px;overflow:hidden}
body{font-family:"Raleway",sans-serif;color:var(--text);background:var(--white);position:relative}
.container{width:1050px;margin:0 auto;position:relative}
a{color:inherit;text-decoration:none}

/* top bar */
.topbar{height:46px;background:var(--light);font-size:14px;color:#444}
.topbar .container{display:flex;justify-content:space-between;align-items:center;height:46px}
.topbar .info{display:flex;gap:10px;align-items:center}
.topbar .sep{color:#999}
.topbar .item{display:flex;align-items:center;gap:6px}
.topbar .actions{display:flex;gap:12px;color:var(--blue);font-weight:600}
.topbar svg{width:13px;height:13px;fill:var(--red)}

/* header */
.header{height:84px;background:var(--white);border-bottom:1px solid #e6e6e6}
.header .container{display:flex;justify-content:space-between;align-items:center;height:84px}
.logo{display:flex;align-items:center;gap:10px;font-weight:700;font-size:26px;color:var(--blue)}
.logo .mark{width:22px;height:22px;background:var(--blue)}
.nav{display:flex;gap:30px;font-size:15px;font-weight:500;color:var(--dark);align-items:center}
.nav .active{background:var(--blue);color:var(--white);padding:9px 14px;border-radius:3px;border:2px solid #003a75}

/* hero */
.hero{height:515px;position:relative;background:linear-gradient(100deg,#d9dee2 0%,#b8c2cb 35%,#6b7480 55%,#e8d9c8 78%,#c9b9a6 100%)}
.hero .container{padding-top:190px}
.hero h1{color:var(--red);font-size:45px;font-weight:700;margin-bottom:14px}
.hero p{color:var(--dark);font-size:21px;font-weight:600;line-height:1.5;width:590px}
.dots{display:flex;gap:10px;margin-top:30px}
.dots span{width:13px;height:13px;border-radius:50%;background:#555}
.dots span:first-child{background:var(--blue)}

/* sections */
.section-title{color:var(--blue);font-size:27px;font-weight:600;text-align:center}
.welcome{height:235px;padding-top:42px}
.welcome p{margin-top:26px;font-size:14px;line-height:26px;text-align:center;padding:0 10px}

.what{height:401px;background:var(--gray-band)}
.what .container{display:flex;gap:45px;padding-top:57px}
.what .photo{width:470px;height:288px;flex:none;border-radius:3px;background:linear-gradient(135deg,#e8e2d4,#5a7fa8 55%,#2d3440)}
.what h2{color:var(--blue);font-size:27px;font-weight:500;margin-top:-4px}
.what h3{color:var(--red);font-size:20px;font-weight:600;line-height:28px;margin-top:8px}
.what p{font-size:14px;line-height:26px;margin-top:14px}
.btn{display:inline-block;margin-top:28px;border:2px solid var(--red);color:var(--dark);font-weight:600;font-size:15px;padding:14px 36px;border-radius:3px;background:var(--white)}

.solutions{height:476px;padding-top:42px}
.solutions .lead{text-align:center;font-size:14px;margin-top:22px}
.cards{display:grid;grid-template-columns:repeat(3,1fr);gap:30px;margin-top:40px;text-align:center}
.icon-ring{width:130px;height:130px;border:3px solid var(--blue);border-radius:50%;margin:0 auto;display:flex;align-items:center;justify-content:center}
.icon-ring svg{width:70px;height:70px}
.cards h4{color:var(--red);font-size:20px;font-weight:600;margin-top:26px}
.cards p{font-size:14px;line-height:25px;margin-top:10px;padding:0 10px}

.testimonial{height:435px;background:var(--blue);color:var(--white);text-align:center;padding-top:48px;position:relative}
.testimonial h2{font-size:27px;font-weight:600}
.testimonial blockquote{font-style:italic;font-size:15.5px;line-height:31px;margin:26px auto 0;width:1050px}
.avatar{width:74px;height:74px;border-radius:50%;margin:30px auto 0;position:relative;background:linear-gradient(135deg,#d6dde4,#8ba0b3);border:3px solid var(--white)}
.avatar .q{position:absolute;right:-14px;bottom:-6px;width:34px;height:34px;border-radius:50%;background:var(--red);display:flex;align-items:center;justify-content:center}
.testimonial .name{font-weight:700;font-size:15px;margin-top:18px}
.testimonial .loc{font-style:italic;font-size:11px;margin-top:6px}
.arrow{position:absolute;top:190px;width:20px;height:30px}
.arrow.left{left:42px}.arrow.right{right:42px}

.blog{height:504px;padding-top:40px}
.posts{display:grid;grid-template-columns:repeat(3,330px);gap:30px;margin-top:32px}
.post .thumb{height:194px}
.post:nth-child(1) .thumb{background:linear-gradient(135deg,#d8d2c4,#8f8a82 60%,#3d3a36)}
.post:nth-child(2) .thumb{background:linear-gradient(135deg,#f0eeea,#b9b4ac 50%,#4b5158)}
.post:nth-child(3) .thumb{background:linear-gradient(135deg,#e7e4de,#c5a98a 45%,#2d3036)}
.post h4{color:var(--red);font-size:20px;font-weight:600;margin-top:20px}
.post p{font-size:14px;line-height:25px;margin-top:10px}
.post .date{color:var(--blue);font-size:12px;font-weight:500;margin-top:10px}

.footer{height:207px;background:linear-gradient(180deg,#2f2f2f,#454545 60%,#3a3a3a);color:#ddd}
.footer .container{height:207px}
.footer .logo{position:absolute;top:42px;left:0;color:var(--white)}
.footer .logo .mark{background:var(--white)}
.footer .fnav{position:absolute;top:38px;right:0;display:flex;gap:26px;font-size:13.5px}
.footer .copy{position:absolute;top:128px;left:0;font-size:11.5px;line-height:24px}
.footer .connect{position:absolute;top:108px;right:0;display:flex;align-items:center;gap:8px;font-size:17px;color:var(--white)}
.footer .connect span.c{width:28px;height:28px;border-radius:50%;background:var(--white)}
</style>
</head>
<body>

<div class="topbar">
  <div class="container">
    <div class="info">
      <span class="item"><svg viewBox="0 0 16 16"><path d="M3 1h3l1.5 4-2 1.2a9 9 0 0 0 4.3 4.3L11 8.5l4 1.5v3a2 2 0 0 1-2 2A12 12 0 0 1 1 3a2 2 0 0 1 2-2z"/></svg>1-800-555-0142</span>
      <span class="sep">|</span>
      <span class="item"><svg viewBox="0 0 16 16"><path d="M1 3h14v10H1zM1 3l7 6 7-6" stroke="#fff" stroke-width="1.2"/></svg>info@brimlowortholink.com</span>
      <span class="sep">|</span>
      <span class="item"><svg viewBox="0 0 16 16"><path d="M8 0a5.5 5.5 0 0 0-5.5 5.5C2.5 10 8 16 8 16s5.5-6 5.5-10.5A5.5 5.5 0 0 0 8 0zm0 8a2.5 2.5 0 1 1 0-5 2.5 2.5 0 0 1 0 5z"/></svg>412 Harwell Lane, Denver, CO 80203</span>
    </div>
    <div class="actions">
      <span class="item"><svg viewBox="0 0 16 16"><path d="M1 2h14v9H6l-4 3v-3H1z"/></svg>Live Chat</span>
      <span class="sep">|</span>
      <span class="item"><svg viewBox="0 0 16 16"><circle cx="8" cy="4.5" r="3.5"/><path d="M1 16a7 7 0 0 1 14 0z"/></svg>Log In</span>
    </div>
  </div>
</div>

<header class="header">
  <div class="container">
    <div class="logo"><span class="mark"></span>Brimlow OrthoLink IT</div>
    <nav class="nav">
      <a class="active">Home</a><a>About Us</a><a>Services</a><a>Solution</a><a>Latest News</a><a>Blog</a><a>Clients</a><a>Contact Us</a>
    </nav>
  </div>
</header>

<section class="hero" role="img" aria-label="Photo of a dentist and a patient looking at dental X-ray images on a computer monitor">
  <div class="container">
    <h1>Welcome to Brimlow OrthoLink</h1>
    <p>Our company is dedicated to installation and service of computer systems in Dental Offices</p>
    <div class="dots"><span></span><span></span><span></span><span></span></div>
  </div>
</section>

<section class="welcome">
  <div class="container">
    <h2 class="section-title">Welcome to Our Website</h2>
    <p>Aliquam molestie, mi et imperdiet euismod, dui purus auctor tellus, et interdum lacus lectus et ante. Sed accumsan sollicitudin sapien, sit amet adipiscing turpis gravida ac. In congue, neque ac lobortis volutpat, libero mauris varius mi, vitae suscipit ipsum ligula vitae risus. Duis aliquam nibh a dui iaculis viverra id a velit. Vivamus egestas risus in magna varius commodo. Sed semper viverra egestas. Etiam pretium porttitor lectus, vel ornare neque porta volutpat.</p>
  </div>
</section>

<section class="what">
  <div class="container">
    <div class="photo" role="img" aria-label="Photo of a dental X-ray unit beside a computer monitor showing a panoramic X-ray"></div>
    <div class="copy">
      <h2>What We Do</h2>
      <h3>Dedicated to Installation and Service of<br>Computer Systems in Dental Offices</h3>
      <p>Aliquam molestie, mi et imperdiet euismod, dui purus auctor tellus, et nterdum lacus lectus et ante. Sed accumsan sollicitudin sapien, sit amet adipiscing turpis gravida ac. In congue, neque ac lobortis volutpat, libero mauris varius mi, vitae suscipit ipsum ligula vitae risus.</p>
      <a class="btn">Read More</a>
    </div>
  </div>
</section>

<section class="solutions">
  <div class="container">
    <h2 class="section-title">Solution We Provide</h2>
    <p class="lead">Aliquam molestie, mi et imperdiet euismod, dui purus auctor tellus, et interdum lacus lectus et ante.</p>
    <div class="cards">
      <div>
        <div class="icon-ring"><svg viewBox="0 0 70 70" fill="#333"><path d="M6 28h8l10-8v30l-10-8H6z"/><rect x="30" y="16" width="34" height="26" rx="2"/><rect x="34" y="20" width="26" height="18" fill="#fff"/><rect x="40" y="44" width="14" height="4"/><rect x="34" y="50" width="26" height="3"/><rect x="30" y="44" width="7" height="14" rx="1"/></svg></div>
        <h4>Audio Visual</h4>
        <p>Sed accumsan sollicitudin sapien, sit amet adipiscing turpis gravida ac. In congue, neque ac lobortis volutpat...</p>
      </div>
      <div>
        <div class="icon-ring"><svg viewBox="0 0 70 70" fill="none" stroke="#333" stroke-width="3"><rect x="6" y="8" width="20" height="14"/><rect x="44" y="8" width="20" height="14"/><rect x="6" y="44" width="20" height="14"/><rect x="44" y="44" width="20" height="14"/><path d="M26 15h18M16 22v22M54 22v22M26 51h18"/></svg></div>
        <h4>Computer Systems &amp; Networks</h4>
        <p>Sed accumsan sollicitudin sapien, sit amet adipiscing turpis gravida ac. In congue, neque ac lobortis volutpat...</p>
      </div>
      <div>
        <div class="icon-ring"><svg viewBox="0 0 70 70"><path d="M22 30a9 9 0 0 1 5-16 12 12 0 0 1 22 3 8 8 0 0 1 0 13z" fill="#333"/><path d="M35 30v10M14 40h42M14 40v6M35 40v6M56 40v6" stroke="#333" stroke-width="2" fill="none"/><g fill="none" stroke="#333" stroke-width="2.5"><rect x="5" y="47" width="18" height="12"/><rect x="26" y="47" width="18" height="12"/><rect x="47" y="47" width="18" height="12"/></g></svg></div>
        <h4>Cloud Services</h4>
        <p>Sed accumsan sollicitudin sapien, sit amet adipiscing turpis gravida ac. In congue, neque ac lobortis volutpat...</p>
      </div>
    </div>
  </div>
</section>

<section class="testimonial">
  <svg class="arrow left" viewBox="0 0 20 30"><path d="M16 3 4 15l12 12" stroke="#fff" stroke-width="2.5" fill="none"/></svg>
  <svg class="arrow right" viewBox="0 0 20 30"><path d="M4 3l12 12L4 27" stroke="#fff" stroke-width="2.5" fill="none"/></svg>
  <h2>What Our Client Says...</h2>
  <blockquote>"Aliquam molestie, mi et imperdiet euismod, dui purus auctor tellus, et interdum lacus lectus et ante. Sed accumsan sollicitudin sapien, sit amet adipiscing turpis gravida ac. In congue, neque ac lobortis volutpat, libero mauris varius mi, vitae suscipit ipsum ligula vitae risus. Duis aliquam nibh a dui iaculis viverra id a velit. Vivamus egestas risus in magna varius commodo."</blockquote>
  <div class="avatar" role="img" aria-label="Client portrait photo">
    <span class="q"><svg width="16" height="12" viewBox="0 0 16 12" fill="#fff"><path d="M0 12V6l3-6h3L4 6h3v6zM9 12V6l3-6h3l-2 6h3v6z"/></svg></span>
  </div>
  <p class="name">Name Heading</p>
  <p class="loc">Location Name Gose Here</p>
</section>

<section class="blog">
  <div class="container">
    <h2 class="section-title">Latest Blog Posts</h2>
    <div class="posts">
      <article class="post">
        <div class="thumb" role="img" aria-label="Photo of two technicians working on a desktop computer"></div>
        <h4>Consectetur Adipiscing</h4>
        <p>Sed accumsan sollicitudin sapien, sit amet adipiscing turpis gravida ac. In congue, neque ac lobortis volutpat...</p>
        <p class="date">Posted on 3 hrs ago</p>
      </article>
      <article class="post">
        <div class="thumb" role="img" aria-label="Photo of a receptionist at a laptop speaking with a patient"></div>
        <h4>Consectetur Adipiscing</h4>
        <p>Sed accumsan sollicitudin sapien, sit amet adipiscing turpis gravida ac. In congue, neque ac lobortis volutpat...</p>
        <p class="date">Posted on 3 hrs ago</p>
      </article>
      <article class="post">
        <div class="thumb" role="img" aria-label="Photo of a dental professional reviewing X-rays on a monitor"></div>
        <h4>Consectetur Adipiscing</h4>
        <p>Sed accumsan sollicitudin sapien, sit amet adipiscing turpis gravida ac. In congue, neque ac lobortis volutpat...</p>
        <p class="date">Posted on 3 hrs ago</p>
      </article>
    </div>
  </div>
</section>

<footer class="footer">
  <div class="container">
    <div class="logo"><span class="mark"></span>Brimlow OrthoLink IT</div>
    <nav class="fnav"><a>Home</a><a>About Us</a><a>Services</a><a>Solution</a><a>Latest News</a><a>Blog</a><a>Clients</a><a>Contact Us</a></nav>
    <div class="copy">Copyright © 2016. BrimlowOrthoLinkIT. All Right Reserved<br>Privacy Policy &nbsp;|&nbsp; Terms of Services</div>
    <div class="connect">Connect Us:&nbsp;<span class="c"></span><span class="c"></span><span class="c"></span><span class="c"></span><span class="c"></span></div>
  </div>
</footer>

</body>
</html>
```